Dental office stationary (letterhead, envelopes), business cards, presentation folders

Nothing too dental outside of the logo. I will need all stationary, presentation folders, business cards. Would prefer to stay in the colors of the logo

Gordon Patel, DDS
Bright Haven Dental Implant Center
555-318-2790
info@brighthavendental.example
4817 NW Maple Crest Rd Unit B
Stuart, FL 00000

Also need appointment date and time
And cancellation policy
I want it to say “kindly ask for
A 48hr cancellation policy to avoid incurring a cancellation fee”

Industry/Entity Type

Dental

Colors
0054AA
0677BA
7BADD7
CADEEF
E8F1F8

Requirements
Must have
• Name of your office, name of doctor, address, phone number
Should not have
• Too much tooth/dental. Only the tooth in logo

```html
<!DOCTYPE html>
<html lang="en">
<head>
<meta charset="utf-8">
<title>Bright Haven Dental Implant Center – Stationery</title>
<link rel="stylesheet" href="https://fonts.googleapis.com/css2?family=Montserrat:wght@400;500;600&family=Parisienne&display=swap">
<style>
  :root{
    --blue-deep:#0054AA;
    --blue:#0677BA;
    --blue-mid:#2B7FD0;
    --blue-soft:#7BADD7;
    --blue-pale:#CADEEF;
    --blue-mist:#E8F1F8;
    --ink:#1d1d1f;
    --paper:#ffffff;
    --night:#141416;
    --stage:#b9b8ba;
  }
  *{box-sizing:border-box;margin:0;padding:0}
  html,body{width:1200px;height:627px;overflow:hidden}
  body{background:var(--stage);font-family:'Montserrat',sans-serif;color:var(--ink);position:relative}
  .sheet{position:absolute;background:var(--paper);box-shadow:0 2px 6px rgba(0,0,0,.18)}
  .brand{font-family:'Montserrat',sans-serif;font-weight:500;color:var(--blue-deep);letter-spacing:.06em;white-space:nowrap}

  /* Letterhead */
  .letterhead{left:74px;top:76px;width:349px;height:494px}
  .letterhead .brand{position:absolute;left:18px;top:40px;font-size:19px}
  .letterhead .divider{position:absolute;left:200px;top:21px;width:1px;height:52px;background:var(--blue-deep)}
  .contact{position:absolute;font-size:6.4px;line-height:8.3px;white-space:nowrap}
  .contact .office{color:var(--blue)}
  .contact .gap{height:5px}
  .contact .row{display:flex;align-items:center;gap:3px}
  .icon{width:6px;height:6px;flex:none;fill:var(--blue-deep)}
  .letterhead .contact{left:216px;top:21px;font-size:6.2px}
  .letter{position:absolute;left:17px;top:113px;width:315px;font-size:7px;line-height:7.9px}
  .letter p{margin-bottom:8px}
  .letter .salute{font-size:8.6px;font-weight:500;margin:10px 0 10px}
  .letter .body{text-align:justify;font-size:6.7px;line-height:7.7px;margin-bottom:7.5px}
  .letter .regards{margin-top:14px}
  .letter .signature{font-family:'Parisienne',cursive;font-size:15px;margin-top:36px}

  /* Folder outside */
  .folder-front{left:470px;top:78px;width:170px;height:218px}
  .folder-front .brand{position:absolute;left:0;right:0;top:60px;text-align:center;font-size:15px}
  .folder-front .contact{left:14px;bottom:14px;font-size:5.6px;line-height:7.4px}
  .folder-back{left:640px;top:78px;width:170px;height:218px;background:linear-gradient(160deg,#2a2a2e,var(--night) 60%)}
  .folder-back .brand{position:absolute;left:0;right:0;top:96px;text-align:center;font-size:15px;color:var(--blue-mid)}

  /* Folder inside */
  .folder-inside{left:470px;top:310px;width:340px;height:238px;background:linear-gradient(90deg,#e9e9eb,#fff 45%,#e4e4e6 50%,#fff 56%)}
  .pocket{position:absolute;bottom:0;height:88px;width:170px;background:linear-gradient(180deg,var(--blue-mid),var(--blue))}
  .pocket.left{left:0;border-top-right-radius:28px}
  .pocket.right{right:0;border-top-left-radius:28px}
  .insert{position:absolute;left:186px;top:16px;width:140px;height:186px;background:var(--paper);box-shadow:0 1px 4px rgba(0,0,0,.15)}
  .insert .brand{position:absolute;left:9px;top:17px;font-size:6.5px}
  .insert .divider{position:absolute;left:84px;top:8px;width:1px;height:20px;background:var(--blue-deep)}
  .bars{position:absolute;left:9px;right:9px}
  .bars i{display:block;height:2px;background:#c9c9cc;margin-bottom:2.4px}

  /* Envelopes */
  .env-back{left:893px;top:76px;width:235px;height:104px;overflow:hidden}
  .env-back .flap{position:absolute;left:0;right:0;top:0;height:37px;background:linear-gradient(180deg,var(--blue),var(--blue-mid));border-radius:0 0 12px 12px}
  .env-back .dot{position:absolute;left:107px;top:8px;width:20px;height:20px;border-radius:50%;border:2.5px solid #fff}
  .env-front{left:893px;top:196px;width:235px;height:102px}
  .env-front .brand{position:absolute;left:10px;top:16px;font-size:7px}
  .env-front .divider{position:absolute;left:80px;top:8px;width:1px;height:18px;background:var(--blue-deep)}
  .env-front .contact{left:88px;top:9px;font-size:3.8px;line-height:5px}

  /* Cards */
  .card{border-radius:10px}
  .card-front{left:915px;top:315px;width:213px;height:122px;background:linear-gradient(160deg,#2d2d31,var(--night) 65%)}
  .card-front .brand{position:absolute;left:0;right:0;top:50px;text-align:center;font-size:19px;color:var(--blue-mid)}
  .card-back{left:915px;top:449px;width:213px;height:122px}
  .card-back .brand{position:absolute;left:11px;top:63px;font-size:10px}
  .card-back .divider{position:absolute;left:106px;top:25px;width:1px;height:76px;background:var(--blue-deep)}
  .card-back .contact{left:115px;top:24px;font-size:4.6px;line-height:6.6px}
  .card-back .title{font-size:8.2px;font-weight:600;color:var(--blue-deep);line-height:10px}
</style>
</head>
<body>

<svg width="0" height="0" style="position:absolute" aria-hidden="true">
  <symbol id="i-phone" viewBox="0 0 10 10"><path d="M2 1h2l1 2.3-1.2.8a5.5 5.5 0 0 0 2.1 2.1l.8-1.2L9 6v2c0 .6-.4 1-1 1A8 8 0 0 1 1 2c0-.6.4-1 1-1z"/></symbol>
  <symbol id="i-mail" viewBox="0 0 10 10"><path d="M1 2.5h8v5H1z M1 2.5l4 3 4-3" fill="none" stroke="currentColor" stroke-width="1"/></symbol>
  <symbol id="i-web" viewBox="0 0 10 10"><circle cx="5" cy="5" r="4"/><path d="M1 5h8M5 1c-2 2.5-2 5.5 0 8M5 1c2 2.5 2 5.5 0 8" fill="none" stroke="#fff" stroke-width=".7"/></symbol>
</svg>

<!-- Letterhead -->
<section class="sheet letterhead" aria-label="Letterhead">
  <div class="brand">BRIGHT HAVEN</div>
  <div class="divider"></div>
  <div class="contact">
    <div class="office">Bright Haven Dental Implant Center</div>
    <div>4817 NW Maple Crest Rd Unit B</div>
    <div>Harborview, ST 00000</div>
    <div class="gap"></div>
    <div class="row"><svg class="icon"><use href="#i-phone"/></svg>555-318-2790</div>
    <div class="row"><svg class="icon" style="color:var(--blue-deep);fill:none"><use href="#i-mail"/></svg>info@brighthavendental.example</div>
    <div class="row"><svg class="icon"><use href="#i-web"/></svg>www.brighthavendental.example</div>
  </div>
  <div class="letter">
    <p>January-03-2020</p>
    <p>Mr, John Doe<br>President</p>
    <p>Northwind Corporation<br>123 Street Name, Suite# 10<br>City, State, 120023</p>
    <p class="salute">Dear Mr, John</p>
    <p class="body">Lorem ipsum dolor sit amet, consectetur adipiscing elit, sed do eiusmod tempor incididunt ut labore et dolore magna aliqua. Ut enim ad minim veniam, quis nostrud exercitation ullamco laboris nisi ut aliquip ex ea commodo consequat. Duis aute irure dolor in reprehenderit in voluptate velit esse cillum dolore eu fugiat nulla pariatur.</p>
    <p class="body">Lorem ipsum dolor sit amet, consectetur adipiscing elit, sed do eiusmod tempor incididunt ut labore et dolore magna aliqua. Ut enim ad minim veniam, quis nostrud exercitation ullamco laboris nisi ut aliquip ex ea commodo consequat. Duis aute irure dolor in reprehenderit in voluptate velit esse cillum dolore eu fugiat nulla pariatur.</p>
    <p class="body">Lorem ipsum dolor sit amet, consectetur adipiscing elit, sed do eiusmod tempor incididunt ut labore et dolore magna aliqua. Ut enim ad minim veniam, quis nostrud exercitation ullamco laboris nisi ut aliquip ex ea commodo consequat.</p>
    <p class="body">Excepteur sint occaecat cupidatat non proident, sunt in culpa qui officia deserunt mollit anim id est laborum. re et dolore magnam aliquam quaerat voluptatem.</p>
    <p class="regards">Regards</p>
    <p class="signature">Daniel Reyes</p>
  </div>
</section>

<!-- Presentation folder, outside -->
<section class="sheet folder-front" aria-label="Folder front cover">
  <div class="brand">BRIGHT HAVEN</div>
  <div class="contact">
    <div class="office">Bright Haven Dental Implant Center</div>
    <div>4817 NW Maple Crest Rd Unit B, Harborview, ST 00000</div>
    <div class="row"><svg class="icon"><use href="#i-phone"/></svg>555-318-2790</div>
    <div class="row"><svg class="icon" style="color:var(--blue-deep);fill:none"><use href="#i-mail"/></svg>info@brighthavendental.example</div>
    <div class="row"><svg class="icon"><use href="#i-web"/></svg>www.brighthavendental.example</div>
  </div>
</section>
<section class="sheet folder-back" role="img" aria-label="Folder back cover, dark surface with subtle repeating pattern">
  <div class="brand">BRIGHT HAVEN</div>
</section>

<!-- Presentation folder, inside -->
<section class="sheet folder-inside" aria-label="Folder inside with pockets">
  <div class="insert" aria-label="Letterhead insert">
    <div class="brand">BRIGHT HAVEN</div>
    <div class="divider"></div>
    <div class="bars" style="left:90px;top:9px"><i style="width:40px;background:var(--blue-soft)"></i><i style="width:34px"></i><i style="width:24px"></i><i style="width:30px"></i><i style="width:36px"></i></div>
    <div class="bars" style="top:42px"><i style="width:30px"></i><i style="width:22px"></i><i style="width:18px"></i><i style="width:34px;margin-top:5px"></i><i style="width:40px"></i><i style="width:30px"></i><i style="width:26px;background:#9c9ca0;margin-top:5px"></i><i></i><i></i><i></i><i style="width:60%"></i><i style="margin-top:4px"></i><i></i><i></i><i style="width:55%"></i></div>
  </div>
  <div class="pocket left"></div>
  <div class="pocket right"></div>
</section>

<!-- Envelope, back -->
<section class="sheet env-back" aria-label="Envelope back">
  <div class="flap"><div class="dot"></div></div>
</section>

<!-- Envelope, front -->
<section class="sheet env-front" aria-label="Envelope front">
  <div class="brand">BRIGHT HAVEN</div>
  <div class="divider"></div>
  <div class="contact">
    <div class="office">Bright Haven Dental Implant Center</div>
    <div>4817 NW Maple Crest Rd Unit B</div>
    <div>Harborview, ST 00000</div>
  </div>
</section>

<!-- Business card, front -->
<section class="sheet card card-front" role="img" aria-label="Business card front, dark surface with subtle repeating pattern">
  <div class="brand">BRIGHT HAVEN</div>
</section>

<!-- Business card, back -->
<section class="sheet card card-back" aria-label="Business card back">
  <div class="brand">BRIGHT HAVEN</div>
  <div class="divider"></div>
  <div class="contact">
    <div class="title">Name of Doctor</div>
    <div>Gordon Patel, DDS</div>
    <div>Bright Haven Dental Implant Center</div>
    <div class="gap"></div>
    <div>4817 NW Maple Crest Rd Unit B</div>
    <div>Harborview, ST 00000</div>
    <div class="gap"></div>
    <div class="row"><svg class="icon" style="width:5px;height:5px"><use href="#i-phone"/></svg>555-318-2790</div>
    <div class="row"><svg class="icon" style="width:5px;height:5px;color:var(--blue-deep);fill:none"><use href="#i-mail"/></svg>info@brighthavendental.example</div>
    <div class="row"><svg class="icon" style="width:5px;height:5px"><use href="#i-web"/></svg>www.brighthavendental.example</div>
  </div>
</section>

</body>
</html>
```